Small Business Broker Business Card Design

A business card design for a small business brokerage, which is a financial service, not unlike real estate brokerage, but for small businesses such as laundromats, pizza shops, restaurants, cleaners etc. The designs should all be simple, more conservative in nature, using the colors and font of the logo. Again, think real estate Brokerage as a business context
Contact Information for Business Card
Name: Glen R. Harlow. Title: Small Business Advisor. Email: g.harlow@bayfieldcapitalworks.example. Mobile: (555) 274-3918. Office: (555) 806-2147. www.bayfieldcapitalworks.example

```html
<!DOCTYPE html>
<html lang="en">
<head>
<meta charset="utf-8">
<title>Bayfield Capital Works – Business Card</title>
<link href="https://fonts.googleapis.com/css2?family=Montserrat:wght@400;700;800&display=swap" rel="stylesheet">
<style>
  :root {
    --navy: #1f3a6b;
    --green: #8cc63f;
    --white: #ffffff;
    --ink: #1f3a6b;
    --backdrop: #e9ebef;
  }
  * { box-sizing: border-box; margin: 0; padding: 0; }
  html, body { width: 1200px; height: 900px; overflow: hidden; }
  body {
    background: var(--backdrop);
    font-family: "Montserrat", sans-serif;
    display: flex;
    flex-direction: column;
    align-items: center;
    justify-content: center;
    gap: 44px;
  }
  .card {
    width: 630px;
    height: 360px;
    border-radius: 16px;
    position: relative;
    overflow: hidden;
    box-shadow: 0 6px 18px rgba(20, 30, 50, 0.18);
  }

  /* Front */
  .card-front {
    background: var(--navy);
    display: flex;
    align-items: center;
    justify-content: center;
  }
  .brand-lockup { display: flex; align-items: center; gap: 16px; }
  .brand-square { width: 30px; height: 30px; background: var(--green); flex: none; }
  .brand-name {
    color: var(--white);
    font-weight: 700;
    font-size: 25px;
    letter-spacing: 1.5px;
    text-transform: uppercase;
    line-height: 1;
  }

  /* Back */
  .card-back { background: var(--white); }
  .bottom-band {
    position: absolute; left: 0; right: 0; bottom: 0;
    height: 12px; background: var(--green);
  }
  .company-mark {
    position: absolute; right: 42px; top: 40px;
    display: flex; align-items: center; gap: 10px;
  }
  .company-square { width: 14px; height: 14px; background: var(--green); flex: none; }
  .company-name {
    color: var(--ink); font-weight: 700; font-size: 14px;
    letter-spacing: 0.8px; text-transform: uppercase; line-height: 1;
  }
  .person { position: absolute; left: 42px; top: 158px; }
  .person-name { color: var(--ink); font-weight: 800; font-size: 31px; line-height: 1.1; }
  .person-title { color: var(--ink); font-weight: 400; font-size: 15px; margin-top: 2px; }
  .divider {
    position: absolute; left: 42px; right: 42px; top: 230px;
    height: 1.5px; background: var(--green);
  }
  .contact-list {
    position: absolute; left: 42px; top: 244px;
    list-style: none;
  }
  .contact-item {
    display: flex; align-items: center; gap: 10px;
    color: var(--ink); font-size: 14px; line-height: 21px;
  }
  .contact-icon { width: 13px; height: 13px; flex: none; fill: var(--navy); }
</style>
</head>
<body>

  <section class="card card-front" aria-label="Card front">
    <div class="brand-lockup">
      <span class="brand-square" aria-hidden="true"></span>
      <p class="brand-name">Bayfield Capital Works, Inc</p>
    </div>
  </section>

  <section class="card card-back" aria-label="Card back">
    <div class="company-mark">
      <span class="company-square" aria-hidden="true"></span>
      <p class="company-name">Bayfield Capital Works, Inc</p>
    </div>
    <div class="person">
      <h1 class="person-name">Glen R. Harlow</h1>
      <p class="person-title">Small Business Advisor</p>
    </div>
    <div class="divider"></div>
    <ul class="contact-list">
      <li class="contact-item">
        <svg class="contact-icon" viewBox="0 0 16 16" aria-hidden="true"><path d="M2 5h12v8H2z M4 3h8v3H4z"/><circle cx="8" cy="9" r="2" fill="#fff"/></svg>
        (555) 806-2147
      </li>
      <li class="contact-item">
        <svg class="contact-icon" viewBox="0 0 16 16" aria-hidden="true"><path d="M3.5 1.5l3 3-1.8 1.8a9 9 0 0 0 5 5l1.8-1.8 3 3-2 2C7 14 2 9 1.5 3.5z"/></svg>
        (555) 274-3918
      </li>
      <li class="contact-item">
        <svg class="contact-icon" viewBox="0 0 16 16" aria-hidden="true"><path d="M1 3h14v10H1z"/><path d="M1 3l7 6 7-6" fill="none" stroke="#fff" stroke-width="1.3"/></svg>
        g.harlow@bayfieldcapitalworks.example
      </li>
      <li class="contact-item">
        <svg class="contact-icon" viewBox="0 0 16 16" aria-hidden="true"><circle cx="8" cy="8" r="7"/><path d="M1 8h14M8 1c-3 3-3 11 0 14M8 1c3 3 3 11 0 14" fill="none" stroke="#fff" stroke-width="1"/></svg>
        www.bayfieldcapitalworks.example
      </li>
    </ul>
    <div class="bottom-band"></div>
  </section>

</body>
</html>
```